Ferncliff Capital - Website Design

We need a website design for a new commercial real estate company called Ferncliff Capital. We're effectively commercial mortgage brokers connecting real estate investors to lenders. We need a website that is simple (not busy), elegant, professional, and user-friendly. A lot of the users will be in their 50's and less tech savvy, so a stream-lined design is best. The website will serve as a portal for lenders to review new financing opportunities, as well as for real estate investors to review terms from lenders.
Updates
Just uploaded our logo.
Target Market(s)
Commercial real estate investors and lenders
Industry/Entity Type
Real Estate
Number of Pages Required
1 page
Colors
Designer to choose colors to be used in the design.
Look and feel

```html
<!DOCTYPE html>
<html lang="en">
<head>
<meta charset="utf-8">
<title>Ferncliff Capital</title>
<link href="https://fonts.googleapis.com/css2?family=Open+Sans:wght@400;600;700&display=swap" rel="stylesheet">
<style>
:root{
  --blue:#1e6fc1;
  --blue-light:#3a9ad9;
  --ink:#1c1c1c;
  --text:#555a60;
  --muted:#8a8f96;
  --gray-band:#eeeff1;
  --slate:#5f6674;
  --white:#ffffff;
  --orange:#e8a23a;
  --line:#d9dcdf;
}
*{margin:0;padding:0;box-sizing:border-box}
html,body{width:1200px;height:3051px;overflow:hidden}
body{font-family:"Open Sans",Arial,sans-serif;color:var(--text);background:var(--white);position:relative}
.abs{position:absolute}
.section-title{position:absolute;left:0;width:1200px;text-align:center;font-weight:700;font-size:19px;color:var(--ink);letter-spacing:.3px}
.section-title::after{content:"";display:block;width:44px;height:2px;background:#b8bcc1;margin:22px auto 0}

/* hero */
.hero{position:absolute;left:0;top:0;width:1200px;height:617px;
  background:linear-gradient(180deg,#8fb3d1 0%,#c9c3b4 22%,#d8a36a 32%,#9c8a73 45%,#6f6a66 65%,#4d4a4a 100%)}
.brand{position:absolute;left:130px;top:18px;font-size:24px;font-weight:600;color:var(--white)}
.nav{position:absolute;top:16px;left:618px;display:flex;align-items:center;gap:6px}
.nav a{font-size:11.5px;font-weight:600;color:var(--white);text-decoration:none;padding:7px 11px;letter-spacing:.3px}
.nav a.active{background:var(--blue)}
.nav .search{width:30px;height:30px;border:2px solid var(--white);border-radius:50%;margin-left:6px;display:flex;align-items:center;justify-content:center}
.hero h1{position:absolute;left:0;top:152px;width:1200px;text-align:center;color:var(--white);font-size:31px;font-weight:700;line-height:38px;letter-spacing:.5px}
.btn-hero{position:absolute;left:517px;top:254px;width:168px;height:42px;background:var(--blue);border:2px solid #5ea6e0;color:var(--white);font-weight:700;font-size:17px;display:flex;align-items:center;justify-content:center}
.dots{position:absolute;top:572px;left:577px;display:flex;gap:7px}
.dots span{width:8px;height:8px;border-radius:50%;background:var(--white)}
.dots span.on{background:var(--orange)}

/* services */
.service{position:absolute;top:760px;width:200px;text-align:center}
.service svg{display:block;margin:0 auto}
.service h3{font-size:13px;font-weight:600;color:var(--ink);margin-top:30px;line-height:16px;height:34px}
.service p{font-size:11px;line-height:17px;color:var(--text);text-decoration:underline;text-decoration-color:#c4c7cb}

/* what we do */
.what{position:absolute;left:0;top:1043px;width:1200px;height:499px;background:var(--gray-band)}
.what h2{position:absolute;left:130px;top:55px;font-size:19px;color:var(--ink);font-weight:700}
.what .intro{position:absolute;left:132px;top:98px;width:380px;font-size:12px;line-height:22px;text-align:justify;color:#3d4248}
.feature-row{position:absolute;left:130px;display:flex;gap:22px}
.feature-row .ring{width:70px;height:70px;border-radius:50%;background:#f7f7f8;border:2px solid #e2e4e7;display:flex;align-items:center;justify-content:center}
.feature-row h4{font-size:15px;font-weight:600;color:var(--ink);margin-top:6px}
.feature-row p{font-size:11px;line-height:15px;margin-top:6px;text-decoration:underline;text-decoration-color:#c4c7cb;width:200px}
.feature-row .more{font-size:10px;font-weight:700;color:var(--blue);margin-top:6px}
.photo-keys{position:absolute;left:576px;top:21px;width:602px;height:453px;
  background:linear-gradient(180deg,#8e6e5c 0%,#a98f7d 40%,#b9b2a7 62%,#5d7a3d 82%,#4c6a31 100%)}

/* testimonials */
.skyline{position:absolute;left:0;top:1730px;width:1200px;height:202px;background:linear-gradient(180deg,rgba(220,223,227,0) 0%,#eceef0 60%,#e5e7ea 100%)}
.quote{position:absolute;left:370px;top:1678px;width:460px;text-align:center;font-size:12.5px;line-height:23px;color:var(--text)}
.qmark{position:absolute;font-size:60px;color:#d6d8db;font-family:Georgia,serif;line-height:1}
.person{position:absolute;left:0;width:1200px;text-align:center;top:1822px}
.person b{display:block;font-size:15px;color:var(--orange);font-weight:700}
.person span{font-size:11px;color:var(--muted)}

/* blog */
.blog{position:absolute;left:0;top:1932px;width:1200px;height:580px;background:var(--slate)}
.blog .section-title{color:var(--white);top:50px}
.blog .section-title::after{background:#c5c9cf}
.post{position:absolute;top:151px;width:294px;height:358px;background:var(--white)}
.post .thumb{width:294px;height:210px}
.post h3{font-size:13px;font-weight:700;color:var(--ink);margin:22px 25px 0}
.post p{font-size:11.5px;line-height:18px;margin:8px 25px 0;color:#3d4248}
.post .btn{display:inline-block;margin:14px 25px 0;background:var(--blue-light);color:var(--white);font-size:10.5px;font-weight:600;padding:6px 9px}

/* perks */
.perk{position:absolute;top:2555px;width:301px;height:97px;border:1px solid var(--line);display:flex;align-items:flex-start;padding:24px 20px}
.perk svg{flex:none;margin-right:18px}
.perk h4{font-size:11px;font-weight:700;color:var(--ink)}
.perk p{font-size:10.5px;line-height:15px;margin-top:5px;color:#3d4248}

/* footer */
.footer{position:absolute;left:0;top:2705px;width:1200px;height:346px;background:#eef0f2}
.footer .brand-foot{position:absolute;left:130px;top:72px;font-size:24px;font-weight:600;color:#505863}
.footer h5{position:absolute;font-size:11.5px;font-weight:700;color:var(--ink)}
.socials{position:absolute;left:160px;top:146px;display:flex;gap:10px}
.socials span{width:30px;height:30px;border-radius:50%}
.contact{position:absolute;left:421px;top:78px;font-size:11.5px;line-height:18px;color:#4a4f55}
.contact div{display:flex;gap:14px;margin-bottom:14px}
.contact svg{flex:none;margin-top:3px}
.menu{position:absolute;left:667px;top:80px;list-style:none;font-size:12px;line-height:18px;color:#4a4f55}
.email-field{position:absolute;left:829px;top:95px;width:237px;height:38px;background:var(--white);font-size:11px;color:var(--muted);padding:11px 14px}
.signup{position:absolute;left:829px;top:152px;width:84px;height:34px;background:var(--blue);color:var(--white);font-size:11px;font-weight:700;display:flex;align-items:center;justify-content:center}
.footer .rule{position:absolute;left:130px;top:257px;width:940px;height:1px;background:#d5d8dc}
.copyright{position:absolute;left:0;top:293px;width:1200px;text-align:center;font-size:11px;color:#4a4f55}
</style>
</head>
<body>

<header class="hero" role="img" aria-label="Aerial photograph of a dense city skyline at sunset">
  <div class="brand">Ferncliff Capital</div>
  <nav class="nav">
    <a class="active">HOME</a><a>ABOUT US</a><a>SERVICES</a><a>PROPERTIES</a><a>CONTACT US</a>
    <span class="search"><svg width="13" height="13" viewBox="0 0 13 13"><circle cx="5.5" cy="5.5" r="4" fill="none" stroke="#fff" stroke-width="1.6"/><line x1="8.5" y1="8.5" x2="12" y2="12" stroke="#fff" stroke-width="1.6"/></svg></span>
  </nav>
  <h1>COMMERCIAL<br>MORTGAGE BROKERS</h1>
  <div class="btn-hero">LEARN MORE</div>
  <div class="dots"><span></span><span></span><span class="on"></span><span></span></div>
</header>

<section>
  <h2 class="section-title" style="top:667px">OUR SERVICES</h2>

  <div class="service" style="left:122px">
    <svg width="60" height="60" viewBox="0 0 60 60"><circle cx="30" cy="17" r="11" fill="var(--blue)"/><path d="M8 60 V44 Q8 32 22 31 L30 42 L38 31 Q52 32 52 44 V60 Z" fill="var(--blue)"/><path d="M28 34 L32 34 L33 50 L30 54 L27 50 Z" fill="#fff"/></svg>
    <h3>OWNER OCCUPIER</h3>
    <p>There are many variations of passages of Lorem Ipsum available, but the majority have suffered alteration in some form</p>
  </div>
  <div class="service" style="left:365px">
    <svg width="60" height="60" viewBox="0 0 60 60"><path d="M16 26 L32 12 L48 26 H43 V42 H21 V26 Z" fill="var(--blue)"/><rect x="29" y="32" width="6" height="10" fill="#fff"/><path d="M2 46 H18 Q26 46 30 50 H44 Q48 50 48 53 H26 M2 58 H40 L58 46 Q54 42 48 46" fill="none" stroke="var(--blue)" stroke-width="4"/></svg>
    <h3>PROPERTY INVESTMENT</h3>
    <p>There are many variations of passages of Lorem Ipsum available, but the majority have suffered alteration in some form</p>
  </div>
  <div class="service" style="left:624px">
    <svg width="60" height="60" viewBox="0 0 60 60"><circle cx="30" cy="30" r="13" fill="none" stroke="var(--blue)" stroke-width="3.5"/><text x="30" y="36" font-size="16" font-weight="700" text-anchor="middle" fill="var(--blue)" font-family="Open Sans, sans-serif">$</text><path d="M2 14 H18 L24 20 M58 46 H42 L36 40" fill="none" stroke="var(--blue)" stroke-width="5"/></svg>
    <h3>DEVELOPEMNT FINANCE</h3>
    <p>There are many variations of passages of Lorem Ipsum available, but the majority have suffered alteration in some form</p>
  </div>
  <div class="service" style="left:878px">
    <svg width="60" height="60" viewBox="0 0 60 60"><path d="M10 2 H40 L52 14 V58 H10 Z" fill="none" stroke="var(--blue)" stroke-width="3.5"/><path d="M40 2 V14 H52" fill="none" stroke="var(--blue)" stroke-width="3"/><g stroke="var(--blue)" stroke-width="3"><line x1="18" y1="24" x2="44" y2="24"/><line x1="18" y1="32" x2="44" y2="32"/><line x1="18" y1="40" x2="44" y2="40"/><line x1="18" y1="48" x2="44" y2="48"/></g></svg>
    <h3 style="margin-top:24px">SHORT TERM<br>BRIDGING FINANCE</h3>
    <p>There are many variations of passages of Lorem Ipsum available, but the majority have suffered</p>
  </div>
</section>

<section class="what">
  <h2>WHAT WE DO</h2>
  <p class="intro">Making this the first true generator on the Internet. It uses a dictionary of over 200 Latin words, combined with a handful of model sentence structures, to generate Lorem Ipsum which looks reasonable. The generated Lorem Ipsum.</p>
  <div class="feature-row" style="top:215px">
    <div class="ring"><svg width="28" height="28" viewBox="0 0 28 28"><path d="M4 20 L4 24 L8 24 L22 10 L18 6 Z" fill="var(--blue)"/><line x1="2" y1="27" x2="26" y2="27" stroke="var(--blue)" stroke-width="2"/></svg></div>
    <div><h4>Mortgage Application</h4><p>There are many variations of passages of Lorem Ipsum</p><div class="more">READ MORE</div></div>
  </div>
  <div class="feature-row" style="top:339px">
    <div class="ring"><svg width="30" height="30" viewBox="0 0 30 30"><circle cx="9" cy="9" r="8" fill="var(--blue)"/><circle cx="21" cy="9" r="8" fill="var(--blue)"/><circle cx="9" cy="21" r="8" fill="var(--blue)"/><circle cx="21" cy="21" r="8" fill="var(--blue)"/><g stroke="#fff" stroke-width="1.8"><line x1="6" y1="9" x2="12" y2="9"/><line x1="9" y1="6" x2="9" y2="12"/><line x1="18" y1="9" x2="24" y2="9"/><line x1="6" y1="19" x2="12" y2="23"/><line x1="12" y1="19" x2="6" y2="23"/><line x1="18" y1="19" x2="24" y2="19"/><line x1="18" y1="23" x2="24" y2="23"/></g></svg></div>
    <div><h4>Mortgage Calculators</h4><p>There are many variations of passages of Lorem Ipsum</p><div class="more">READ MORE</div></div>
  </div>
  <div class="photo-keys" role="img" aria-label="Photograph of a couple receiving house keys from an agent in front of a brick home"></div>
</section>

<section>
  <div class="skyline" role="img" aria-label="Faint city skyline silhouette"></div>
  <h2 class="section-title" style="top:1600px">TESTIMONIALS</h2>
  <span class="qmark" style="left:325px;top:1662px">&ldquo;</span>
  <p class="quote">It is a long established fact that a reader will be distracted by the readable content of a page when looking at its layout. The point of using Lorem Ipsum is that it has a more-or-less normal distribution of letters, as opposed to using 'Content here, content here', making it look like readable English.</p>
  <span class="qmark" style="left:770px;top:1760px">&rdquo;</span>
  <svg class="abs" style="left:498px;top:1832px" width="12" height="20" viewBox="0 0 12 20"><path d="M10 2 L2 10 L10 18" fill="none" stroke="#9ea3a9" stroke-width="2"/></svg>
  <svg class="abs" style="left:700px;top:1832px" width="12" height="20" viewBox="0 0 12 20"><path d="M2 2 L10 10 L2 18" fill="none" stroke="#9ea3a9" stroke-width="2"/></svg>
  <div class="person"><b>Dana R</b><span>United States</span></div>
</section>

<section class="blog">
  <h2 class="section-title">LATEST BLOG</h2>
  <article class="post" style="left:134px">
    <div class="thumb" role="img" aria-label="Photograph of a city skyline in warm orange light" style="background:linear-gradient(180deg,#f0c04a 0%,#e88a2f 55%,#b43c22 100%)"></div>
    <h3>CONTRARY TO POPULAR BELIEF LOREM</h3>
    <p>There are many variations of passages of Lorem Ipsum available, but the majority.</p>
    <span class="btn">READ MORE</span>
  </article>
  <article class="post" style="left:453px">
    <div class="thumb" role="img" aria-label="Photograph of a resort pool with palm trees at dusk" style="background:linear-gradient(180deg,#c9a4c4 0%,#8f7f9c 40%,#3f5a48 70%,#2c4466 100%)"></div>
    <h3>CONTRARY TO POPULAR BELIEF LOREM</h3>
    <p>There are many variations of passages of Lorem Ipsum available, but the majority.</p>
    <span class="btn">READ MORE</span>
  </article>
  <article class="post" style="left:773px">
    <div class="thumb" role="img" aria-label="Photograph of high-rise buildings under construction with cranes" style="background:linear-gradient(180deg,#f2c9a0 0%,#c9a184 45%,#6d5a52 100%)"></div>
    <h3>CONTRARY TO POPULAR BELIEF LOREM</h3>
    <p>There are many variations of passages of Lorem Ipsum available, but the majority.</p>
    <span class="btn">READ MORE</span>
  </article>
</section>

<section>
  <div class="perk" style="left:132px">
    <svg width="40" height="40" viewBox="0 0 40 40"><g fill="var(--blue)"><ellipse cx="12" cy="12" rx="10" ry="4"/><rect x="2" y="12" width="20" height="6"/><ellipse cx="12" cy="24" rx="10" ry="4"/><rect x="2" y="24" width="20" height="6"/><ellipse cx="12" cy="30" rx="10" ry="4"/></g><circle cx="28" cy="26" r="10" fill="var(--blue)"/><text x="28" y="31" font-size="13" font-weight="700" text-anchor="middle" fill="#fff" font-family="Open Sans, sans-serif">$</text></svg>
    <div><h4>LOW RATES</h4><p>There are many variations of passages of Lorem Ipsum available.</p></div>
  </div>
  <div class="perk" style="left:450px">
    <svg width="40" height="40" viewBox="0 0 40 40"><circle cx="20" cy="16" r="10" fill="var(--blue)"/><text x="20" y="21" font-size="13" font-weight="700" text-anchor="middle" fill="#fff" font-family="Open Sans, sans-serif">$</text><path d="M2 22 L10 34 H16 M38 22 L30 34 H24" fill="none" stroke="var(--blue)" stroke-width="4"/></svg>
    <div><h4>SAVE MONEY</h4><p>There are many variations of passages of Lorem Ipsum available.</p></div>
  </div>
  <div class="perk" style="left:767px">
    <svg width="40" height="40" viewBox="0 0 40 40"><rect x="3" y="11" width="34" height="25" fill="none" stroke="var(--blue)" stroke-width="4"/><path d="M14 11 V5 H26 V11" fill="none" stroke="var(--blue)" stroke-width="4"/><rect x="17" y="20" width="6" height="6" fill="var(--blue)"/></svg>
    <div><h4>EXPERIENCE</h4><p>There are many variations of passages of Lorem Ipsum available.</p></div>
  </div>
</section>

<footer class="footer">
  <div class="brand-foot">Ferncliff Capital</div>
  <h5 style="left:194px;top:120px">FOLLOW US</h5>
  <div class="socials" aria-label="Social links">
    <span style="background:#2f5fa8"></span><span style="background:#2b9fe0"></span><span style="background:#d8463a"></span><span style="background:#3fa39a"></span>
  </div>

  <h5 style="left:421px;top:49px">CONTACT US</h5>
  <div class="contact">
    <div><svg width="9" height="12" viewBox="0 0 9 12"><path d="M4.5 12 L1 6 A4 4 0 1 1 8 6 Z" fill="#4a4f55"/><circle cx="4.5" cy="4.5" r="1.5" fill="#eef0f2"/></svg><span>412 Harbor Lane<br>Millbrook, NM 87001</span></div>
    <div><svg width="11" height="11" viewBox="0 0 11 11"><path d="M1 2 L3 0.5 L5 3 L3.8 4.3 Q5 6.5 6.8 7.2 L8 6 L10.5 8 L9 10 Q3 9.5 1 2 Z" fill="#4a4f55"/></svg><span>555.014.2290</span></div>
    <div><svg width="11" height="9" viewBox="0 0 11 9"><rect width="11" height="9" fill="#4a4f55"/><path d="M0.5 1 L5.5 5 L10.5 1" fill="none" stroke="#eef0f2" stroke-width="1"/></svg><span>info@ferncliffcapital.com</span></div>
  </div>

  <h5 style="left:667px;top:49px">MENU</h5>
  <ul class="menu"><li>Home</li><li>About Us</li><li>Services</li><li>Properties</li><li>Contact us</li></ul>

  <h5 style="left:829px;top:49px">NEWSLETTER SIGNUP</h5>
  <div class="email-field">E-mail id</div>
  <div class="signup">SIGNUP</div>

  <div class="rule"></div>
  <p class="copyright">Copyrights @ 2017 All Rights Reserved</p>
</footer>

</body>
</html>
```